Private Investment Firm Needs PowerPoint Presentation Template

Design PowerPoint template, take Pinebrook-submitted rough presentation draft, and drop it into new template. See attached Project Brief file for more detail.
Updates

Some decent designs have been submitted but they seem to lack the understanding of our target markets. I am hopeful that more time and feedback will result in better results.

Target Market(s)

Private company owners and intermediaries.

Font styles to use
Serif

Colors
3176b5

Requirements
Must have
• See attached Project Brief.
Nice to have
Should not have
• No B2C fluff--this is a B2B project.

```html
<!DOCTYPE html>
<html lang="en">
<head>
<meta charset="utf-8">
<title>The 12 Primary Uses of Non-Control Capital</title>
<link href="https://fonts.googleapis.com/css2?family=Montserrat:wght@400;500;700&family=Libre+Baskerville:wght@400&display=swap" rel="stylesheet">
<style>
  :root {
    --brand-blue: #0b6ec4;
    --title-blue: #1670c0;
    --navy: #244a6b;
    --sky: #4a8fc5;
    --cell-bg: #f2f2f2;
    --cell-border: #dcdcdc;
    --ink: #1f1f1f;
    --white: #ffffff;
  }
  * { box-sizing: border-box; margin: 0; padding: 0; }
  html, body { width: 1200px; height: 676px; overflow: hidden; background: var(--white); }
  .slide {
    position: relative;
    width: 1200px; height: 676px;
    font-family: "Montserrat", Arial, sans-serif;
    color: var(--ink);
    overflow: hidden;
  }
  .side-band { position: absolute; top: 0; left: 0; width: 44px; height: 676px; background: var(--brand-blue); }
  .edge-band { position: absolute; top: 0; right: 0; width: 12px; height: 676px; background: var(--brand-blue); }
  .site-url {
    position: absolute; left: 22px; top: 336px;
    transform: translate(-50%, -50%) rotate(-90deg);
    font-family: "Libre Baskerville", Georgia, serif;
    font-size: 13px; color: var(--white); white-space: nowrap;
  }
  .page-number {
    position: absolute; top: 19px; right: 40px;
    font-family: "Libre Baskerville", Georgia, serif;
    font-size: 17px; color: var(--ink);
  }
  .slide-title {
    position: absolute; top: 80px; left: 0; width: 1176px;
    text-align: center;
    font-weight: 700; font-size: 29px; letter-spacing: 0.3px;
    color: var(--title-blue);
  }
  .row-tab { position: absolute; width: 26px; height: 120px; }
  .row-tab.left { left: 130px; }
  .row-tab.right { left: 1073px; }
  .tier-1 { background: var(--navy); }
  .tier-2 { background: var(--brand-blue); }
  .tier-3 { background: var(--sky); }
  .uses-grid {
    position: absolute; left: 156px; top: 150px;
    width: 917px; height: 406px;
    display: grid;
    grid-template-columns: repeat(4, 1fr);
    grid-template-rows: repeat(3, 1fr);
    gap: 5px 6px;
  }
  .use-card {
    background: var(--cell-bg);
    border: 1px solid var(--cell-border);
    display: flex; flex-direction: column; justify-content: center; align-items: center;
    text-align: center;
    padding: 8px 12px;
  }
  .use-card h2 {
    font-weight: 400; font-size: 15px; line-height: 1.0;
    margin-bottom: 8px; color: var(--ink);
  }
  .use-card p {
    font-size: 9.4px; line-height: 1.55; color: var(--ink);
  }
  .brand {
    position: absolute; left: 68px; top: 616px;
    display: flex; align-items: center; gap: 10px;
  }
  .brand-dot { width: 30px; height: 30px; border-radius: 50%; background: var(--brand-blue); }
  .brand-name {
    font-family: "Montserrat", Arial, sans-serif;
    font-weight: 500; font-size: 16px; letter-spacing: 1px;
    color: var(--navy); text-transform: uppercase;
  }
</style>
</head>
<body>
<div class="slide">
  <div class="side-band"></div>
  <div class="site-url">www.pinebrookcapital.com</div>
  <div class="edge-band"></div>
  <div class="page-number">6</div>

  <h1 class="slide-title">THE 12 PRIMARY USES OF NON-CONTROL CAPITAL</h1>

  <div class="row-tab left tier-1" style="top:157px"></div>
  <div class="row-tab right tier-1" style="top:157px"></div>
  <div class="row-tab left tier-2" style="top:294px"></div>
  <div class="row-tab right tier-2" style="top:294px"></div>
  <div class="row-tab left tier-3" style="top:430px"></div>
  <div class="row-tab right tier-3" style="top:430px"></div>

  <section class="uses-grid">
    <article class="use-card">
      <h2>Growth</h2>
      <p>Capital used to organically expand a business: introduce new products, build a new factory, hire additional management or employees, enter new markets, or for general working capital purposes</p>
    </article>
    <article class="use-card">
      <h2>Acquisitions</h2>
      <p>Capital used to acquire one or more competitors or to allow for further vertical or horizontal integration</p>
    </article>
    <article class="use-card">
      <h2>Partner or Shareholder<br>Buy-Out</h2>
      <p>Capital used to buy-out an inactive or retiring partner or shareholder.</p>
    </article>
    <article class="use-card">
      <h2>Management Buy-Out<br>(MBO)</h2>
      <p>When the incumbent management team buys most or all of the ownership of an inactive founder or executive</p>
    </article>

    <article class="use-card">
      <h2>Management Buy-In<br>(MBI)</h2>
      <p>When an external, experienced executive buys a business from one or more inactive owners and needs additional capital to affect the purchase</p>
    </article>
    <article class="use-card">
      <h2>Family Ownership &amp; Wealth<br>Transfer</h2>
      <p>When junior generations of a family acquire most or all of the ownership interests of more senior generations allowing the business to remain in the family name</p>
    </article>
    <article class="use-card">
      <h2>Balance Sheet<br>Recapitalization</h2>
      <p>Changes the debt and equity mixture of a Company's finances to a more optimal capital structure</p>
    </article>
    <article class="use-card">
      <h2>Refinancing</h2>
      <p>Replacing one form or type of debt with another with better terms, conditions, and flexibility</p>
    </article>

    <article class="use-card">
      <h2>Family Office Support</h2>
      <p>Allows a Family Office to affect an investment in a Company by allowing a junior capital provider to invest alongside them</p>
    </article>
    <article class="use-card">
      <h2>Senior Lender<br>Enhancement or<br>Transition</h2>
      <p>When a Company has grown beyond the means or interest of its senior bank but needs additional capital to support its continuing growth</p>
    </article>
    <article class="use-card">
      <h2>De-Lever Balance Sheet</h2>
      <p>When a Company has taken on too much debt (typically senior debt) and replaces some of it with either equity or other junior capital to provide operating flexibility</p>
    </article>
    <article class="use-card">
      <h2>Owner Dividend<br>(Liquidity)</h2>
      <p>When one or more owners take a non-life changing cash distribution, typically used to diversify their net worth</p>
    </article>
  </section>

  <div class="brand">
    <span class="brand-dot"></span>
    <span class="brand-name">Pinebrook Capital</span>
  </div>
</div>
</body>
</html>
```